US Recruiting Firm Needs Dynamic Tri-Fold Brochure

Need tri-fold professional brochure for HR recruiting and consulting firm based in the US.

Target Market(s)

Clients seeking administrative and human resources talent

Industry/Entity Type

Recruitment

Font styles to use
Sans Serif

Requirements
Should not have
• No weird shapes
• No heavy geometric shapes -- I prefer curvy lines
• Not a dark brochure

```html
<!DOCTYPE html>
<html lang="en">
<head>
<meta charset="utf-8">
<title>Brightline Talent Partners – Tri-Fold Brochure</title>
<link href="https://fonts.googleapis.com/css2?family=Montserrat:wght@600;700;800&family=Open+Sans:wght@400;600;700&display=swap" rel="stylesheet">
<style>
:root{
  --navy:#1c2b5e;
  --pink:#e2237c;
  --green:#8cc63f;
  --blue:#2a9fd6;
  --ink:#4a4f5c;
  --muted:#7b8190;
  --paper:#ffffff;
  --stage:#dcdcdc;
}
*{box-sizing:border-box;margin:0;padding:0}
html,body{width:870px;height:1200px;overflow:hidden;background:var(--stage);font-family:"Open Sans",Arial,sans-serif;color:var(--ink)}
.spread{position:absolute;left:15px;width:840px;height:575px;background:var(--paper);display:flex;box-shadow:0 2px 6px rgba(0,0,0,.18)}
.spread--outside{top:15px}
.spread--inside{top:612px}
.panel{position:relative;width:280px;height:100%;overflow:hidden}
.panel + .panel{border-left:1px solid #eee}
.photo{position:absolute;left:0;width:100%}
.wave{position:absolute;left:0;width:100%;display:block}
.heading{font-family:"Montserrat",Arial,sans-serif;font-weight:700;color:var(--navy)}
.small{font-size:8.5px;line-height:1.5;color:var(--ink)}
.brand{position:absolute;left:0;right:0;text-align:center}
.brand__name{font-family:"Montserrat",Arial,sans-serif;font-weight:700;color:var(--navy);font-size:16px;line-height:1.2}
.brand__tag{font-size:8px;color:var(--muted);margin-top:3px}
.positions{position:absolute;left:22px;top:24px;right:22px}
.positions h2{font-size:11.5px;line-height:1.35;margin-bottom:10px}
.positions ul{list-style:none}
.positions li{font-size:8.5px;line-height:1.55;padding-left:10px;position:relative}
.positions li::before{content:"";position:absolute;left:0;top:5px;width:4px;height:4px;border-radius:50%;background:var(--pink)}
.pill{display:inline-block;background:var(--pink);color:#fff;font-family:"Montserrat",Arial,sans-serif;font-weight:700;font-size:10px;letter-spacing:.5px;padding:6px 20px;border-radius:14px}
.cta{position:absolute;top:262px;left:0;right:0;text-align:center}
.cta p{font-size:10px;line-height:1.45;color:var(--ink);margin:12px 40px 0}
.contact{position:absolute;left:0;right:0;bottom:0;height:168px;background:var(--navy);padding:42px 26px 0}
.contact__row{display:flex;align-items:center;gap:10px;color:#fff;font-size:9.5px;margin-bottom:12px}
.contact__icon{width:22px;height:22px;border-radius:50%;background:var(--pink);display:flex;align-items:center;justify-content:center;flex:none}
.cover-band{position:absolute;left:0;right:0;bottom:0;height:150px}
.cover-band__title{position:absolute;right:20px;bottom:52px;color:#fff;font-family:"Montserrat",Arial,sans-serif;font-weight:700;font-size:14px}
.label{display:inline-block;background:var(--pink);color:#fff;font-family:"Montserrat",Arial,sans-serif;font-weight:700;font-size:10px;padding:5px 14px;border-radius:0 12px 12px 0}
.about{position:absolute;top:218px;left:0;right:0}
.about p{margin:10px 22px 0}
.trusted{position:absolute;top:22px;left:22px;right:22px}
.trusted h2{font-size:11px;text-align:center;margin-bottom:8px}
.why{position:absolute;top:150px;left:0;right:0}
.why__bar{background:var(--pink);color:#fff;text-align:center;font-family:"Montserrat",Arial,sans-serif;font-weight:700;font-size:10.5px;padding:6px 0;margin:0 22px;border-radius:14px}
.ticks{list-style:none;margin:10px 30px 0}
.ticks li{display:flex;align-items:flex-start;gap:7px;font-size:8.5px;line-height:1.4;margin-bottom:3px}
.ticks svg{flex:none;margin-top:1px}
.mission{position:absolute;top:478px;left:22px;right:22px;text-align:center}
.mission h2{font-size:11px;margin-bottom:5px}
.services{position:absolute;top:22px;left:22px;right:22px}
.services h2{color:var(--green);font-size:12px;line-height:1.3;margin-bottom:12px}
</style>
</head>
<body>

<section class="spread spread--outside">

  <div class="panel panel--positions">
    <div class="positions">
      <h2 class="heading">We offer stellar administrative and HR talent. Positions that we fill include:</h2>
      <ul>
        <li>HR Assistant</li><li>HR Coordinator</li><li>Recruiting Coordinator</li>
        <li>HR Generalist</li><li>HR Specialist</li><li>HR Manager</li>
        <li>HR Director</li><li>Payroll Specialist</li><li>Benefits Administrator</li>
        <li>Compensation Analyst</li><li>Training Coordinator</li><li>Office Manager</li>
        <li>Executive Assistant</li><li>Administrative Assistant</li><li>Receptionist</li>
        <li>Office Assistant</li>
      </ul>
    </div>
    <div class="photo" style="top:345px;height:170px;background:linear-gradient(180deg,#b9c7d6,#6f8196)" role="img" aria-label="Photo of business people walking through a bright office"></div>
    <svg class="wave" style="bottom:0" height="90" viewBox="0 0 280 90" preserveAspectRatio="none">
      <path d="M0 30 C90 70 180 0 280 35 L280 90 L0 90 Z" fill="#fff"/>
      <path d="M0 30 C90 70 180 0 280 35" fill="none" stroke="var(--pink)" stroke-width="3"/>
      <path d="M0 42 C90 80 180 12 280 47" fill="none" stroke="var(--green)" stroke-width="3"/>
      <path d="M0 54 C90 90 180 24 280 59" fill="none" stroke="var(--blue)" stroke-width="2"/>
    </svg>
  </div>

  <div class="panel panel--contact">
    <div class="photo" style="top:0;height:190px;background:linear-gradient(160deg,#cfdbe6,#8aa1b6)" role="img" aria-label="Photo of a professional woman working at a computer"></div>
    <svg class="wave" style="top:150px" height="45" viewBox="0 0 280 45" preserveAspectRatio="none">
      <path d="M0 20 C100 50 190 0 280 22 L280 45 L0 45 Z" fill="#fff"/>
      <path d="M0 20 C100 50 190 0 280 22" fill="none" stroke="var(--green)" stroke-width="3"/>
    </svg>
    <div class="brand" style="top:212px">
      <div class="brand__name">Brightline Talent Partners</div>
      <div class="brand__tag">Administrative &amp; HR Placement</div>
    </div>
    <div class="cta">
      <span class="pill">CONTACT US</span>
      <p>To learn more and request a FREE consultation, contact us today.</p>
    </div>
    <div class="contact">
      <div class="contact__row"><span class="contact__icon"><svg width="11" height="11" viewBox="0 0 24 24"><path fill="#fff" d="M6.6 10.8a15 15 0 006.6 6.6l2.2-2.2a1 1 0 011-.25 11 11 0 003.6.6 1 1 0 011 1V20a1 1 0 01-1 1A17 17 0 013 4a1 1 0 011-1h3.5a1 1 0 011 1c0 1.25.2 2.45.6 3.6a1 1 0 01-.25 1z"/></svg></span>555-010-4827</div>
      <div class="contact__row"><span class="contact__icon"><svg width="11" height="11" viewBox="0 0 24 24"><path fill="#fff" d="M3 5h18v14H3z"/><path d="M3 5l9 7 9-7" fill="none" stroke="#e2237c" stroke-width="2"/></svg></span>hello@brightlinetalent.net</div>
      <div class="contact__row"><span class="contact__icon"><svg width="11" height="11" viewBox="0 0 24 24"><circle cx="12" cy="12" r="9" fill="none" stroke="#fff" stroke-width="2"/><path d="M3 12h18M12 3c3 3 3 15 0 18M12 3c-3 3-3 15 0 18" fill="none" stroke="#fff" stroke-width="1.6"/></svg></span>www.brightlinetalent.net</div>
    </div>
    <svg class="wave" style="bottom:150px" height="40" viewBox="0 0 280 40" preserveAspectRatio="none">
      <path d="M0 10 C90 40 190 0 280 18 L280 40 L0 40 Z" fill="var(--navy)"/>
      <path d="M0 10 C90 40 190 0 280 18" fill="none" stroke="var(--pink)" stroke-width="3"/>
    </svg>
  </div>

  <div class="panel panel--cover">
    <div class="brand" style="top:32px">
      <div class="brand__name">Brightline Talent Partners</div>
      <div class="brand__tag">Administrative &amp; HR Placement</div>
    </div>
    <div class="photo" style="top:92px;height:370px;background:linear-gradient(170deg,#d7dde3,#9aa8b5)" role="img" aria-label="Photo of a smiling businesswoman in an office"></div>
    <div class="cover-band">
      <svg class="wave" style="top:0;height:150px" viewBox="0 0 280 150" preserveAspectRatio="none">
        <path d="M0 30 C90 70 180 0 280 25 L280 150 L0 150 Z" fill="var(--navy)"/>
        <path d="M0 22 C90 62 180 -8 280 17" fill="none" stroke="var(--green)" stroke-width="3"/>
        <path d="M0 30 C90 70 180 0 280 25" fill="none" stroke="var(--pink)" stroke-width="3"/>
      </svg>
      <div class="cover-band__title">Administrative &amp; HR Talent</div>
    </div>
  </div>
</section>

<section class="spread spread--inside">

  <div class="panel panel--about">
    <div class="photo" style="top:0;height:200px;background:linear-gradient(160deg,#c4ccd6,#7f8ea0)" role="img" aria-label="Photo of a business team meeting around a table"></div>
    <svg class="wave" style="top:165px" height="40" viewBox="0 0 280 40" preserveAspectRatio="none">
      <path d="M0 18 C100 45 190 0 280 15 L280 40 L0 40 Z" fill="#fff"/>
      <path d="M0 18 C100 45 190 0 280 15" fill="none" stroke="var(--blue)" stroke-width="3"/>
    </svg>
    <div class="about">
      <span class="label">ABOUT US</span>
      <p class="small">Brightline Talent Partners is a recruiting and search firm that focuses on placing administrative and human resources talent with growing companies across the region and beyond.</p>
      <p class="small">Our team brings years of hands-on experience in staffing, so we understand both sides of the hiring table and what it takes to build a lasting match.</p>
      <p class="small">Each search is customized to the client's goals, culture and budget. We screen, interview and reference every candidate, presenting only those who truly fit the role and team.</p>
      <p class="small">Whether you need one hire or a whole department, we are ready to help you find dependable people.</p>
    </div>
  </div>

  <div class="panel panel--why">
    <div class="trusted">
      <h2 class="heading">A TRUSTED RECRUITING PARTNER</h2>
      <p class="small" style="text-align:center">We focus on recruiting and consulting, so we know the market, the talent and the skills that matter. Our process is simple, thorough and built around your timeline and needs.</p>
    </div>
    <div class="why">
      <div class="why__bar">WHY CHOOSE US?</div>
      <ul class="ticks">
        <li><svg width="10" height="10" viewBox="0 0 10 10"><path d="M1 5l3 3 5-6" fill="none" stroke="var(--green)" stroke-width="2"/></svg>Dedicated HR and admin specialists</li>
        <li><svg width="10" height="10" viewBox="0 0 10 10"><path d="M1 5l3 3 5-6" fill="none" stroke="var(--green)" stroke-width="2"/></svg>Fast access to qualified candidates</li>
        <li><svg width="10" height="10" viewBox="0 0 10 10"><path d="M1 5l3 3 5-6" fill="none" stroke="var(--green)" stroke-width="2"/></svg>Thorough screening and interviews</li>
        <li><svg width="10" height="10" viewBox="0 0 10 10"><path d="M1 5l3 3 5-6" fill="none" stroke="var(--green)" stroke-width="2"/></svg>Customized search for every client</li>
        <li><svg width="10" height="10" viewBox="0 0 10 10"><path d="M1 5l3 3 5-6" fill="none" stroke="var(--green)" stroke-width="2"/></svg>Flexible and fair fee structure</li>
        <li><svg width="10" height="10" viewBox="0 0 10 10"><path d="M1 5l3 3 5-6" fill="none" stroke="var(--green)" stroke-width="2"/></svg>Placement guarantee included</li>
      </ul>
    </div>
    <div class="photo" style="top:318px;height:150px;background:linear-gradient(160deg,#d3d9df,#8e9bab)" role="img" aria-label="Photo of hands reviewing documents at a desk"></div>
    <div class="mission">
      <h2 class="heading">OUR MISSION</h2>
      <p class="small">To connect companies with dependable administrative and HR talent through honest, personal service, helping clients and candidates grow together.</p>
    </div>
  </div>

  <div class="panel panel--services">
    <div class="services">
      <h2 class="heading" style="color:var(--green)">We provide customized recruiting and consulting services</h2>
      <ul class="ticks" style="margin:0">
        <li><svg width="10" height="10" viewBox="0 0 10 10"><path d="M1 5l3 3 5-6" fill="none" stroke="var(--pink)" stroke-width="2"/></svg>Position management</li>
        <li><svg width="10" height="10" viewBox="0 0 10 10"><path d="M1 5l3 3 5-6" fill="none" stroke="var(--pink)" stroke-width="2"/></svg>Employee candidate profiles</li>
        <li><svg width="10" height="10" viewBox="0 0 10 10"><path d="M1 5l3 3 5-6" fill="none" stroke="var(--pink)" stroke-width="2"/></svg>Sourcing strategy</li>
        <li><svg width="10" height="10" viewBox="0 0 10 10"><path d="M1 5l3 3 5-6" fill="none" stroke="var(--pink)" stroke-width="2"/></svg>Hiring and interview consulting</li>
        <li><svg width="10" height="10" viewBox="0 0 10 10"><path d="M1 5l3 3 5-6" fill="none" stroke="var(--pink)" stroke-width="2"/></svg>Contract or permanent staffing</li>
        <li><svg width="10" height="10" viewBox="0 0 10 10"><path d="M1 5l3 3 5-6" fill="none" stroke="var(--pink)" stroke-width="2"/></svg>Job description writing</li>
        <li><svg width="10" height="10" viewBox="0 0 10 10"><path d="M1 5l3 3 5-6" fill="none" stroke="var(--pink)" stroke-width="2"/></svg>Candidate assessment</li>
        <li><svg width="10" height="10" viewBox="0 0 10 10"><path d="M1 5l3 3 5-6" fill="none" stroke="var(--pink)" stroke-width="2"/></svg>Confidential executive search</li>
        <li><svg width="10" height="10" viewBox="0 0 10 10"><path d="M1 5l3 3 5-6" fill="none" stroke="var(--pink)" stroke-width="2"/></svg>Reference checking</li>
        <li><svg width="10" height="10" viewBox="0 0 10 10"><path d="M1 5l3 3 5-6" fill="none" stroke="var(--pink)" stroke-width="2"/></svg>Salary benchmarking</li>
        <li><svg width="10" height="10" viewBox="0 0 10 10"><path d="M1 5l3 3 5-6" fill="none" stroke="var(--pink)" stroke-width="2"/></svg>HR policy support</li>
        <li><svg width="10" height="10" viewBox="0 0 10 10"><path d="M1 5l3 3 5-6" fill="none" stroke="var(--pink)" stroke-width="2"/></svg>New hire onboarding</li>
      </ul>
    </div>
    <div class="photo" style="top:345px;height:230px;background:linear-gradient(170deg,#c9d2db,#7e8d9f)" role="img" aria-label="Photo of a confident group of office professionals"></div>
    <svg class="wave" style="top:330px" height="45" viewBox="0 0 280 45" preserveAspectRatio="none">
      <path d="M0 0 L280 0 L280 18 C190 45 90 0 0 25 Z" fill="#fff"/>
      <path d="M280 18 C190 45 90 0 0 25" fill="none" stroke="var(--green)" stroke-width="3"/>
      <path d="M280 26 C190 53 90 8 0 33" fill="none" stroke="var(--pink)" stroke-width="2"/>
    </svg>
  </div>
</section>

</body>
</html>
```